Enhance Landing Page

Actual: https://thecoralparlor.com/aplique-no-litoral-lp-port/

I need a better design for this page:
Using this shortcodes : https://bolder.qrxlayouts.net
Rules:
. Keep the page header
. Keep the footer

```html
<!DOCTYPE html>
<html lang="pt-BR">
<head>
<meta charset="utf-8">
<title>Coral Parlor — Invista na Flórida</title>
<link rel="stylesheet" href="https://fonts.googleapis.com/css2?family=Open+Sans:wght@400;600;700;800&display=swap">
<style>
:root{
  --teal:#1d9cc3;
  --teal-dark:#1788ab;
  --teal-tile:#2fb0d6;
  --orange:#f26522;
  --pink:#e5195f;
  --green:#3cb54a;
  --navy:#1f3f73;
  --ink:#2b2b2b;
  --muted:#666;
  --light:#f2f0f0;
  --dark:#1d1f22;
}
*{box-sizing:border-box;margin:0;padding:0}
html,body{width:1200px;height:5294px;overflow:hidden}
body{font-family:"Open Sans",Arial,sans-serif;color:var(--ink);background:#fff;position:relative}
.abs{position:absolute}
.btn{display:inline-flex;align-items:center;justify-content:center;gap:10px;color:#fff;font-weight:700;text-transform:uppercase;letter-spacing:.5px;border:0}
.rule{width:70px;height:4px;background:var(--teal)}

/* header */
.site-header{position:absolute;top:0;left:0;width:1200px;height:106px;background:#fff;z-index:3}
.contact-mini{position:absolute;left:218px;top:34px;font-size:11px;color:var(--muted)}
.contact-mini .pill{display:inline-block;background:var(--green);color:#fff;font-weight:700;font-size:10px;padding:3px 10px;border-radius:3px;margin-bottom:8px}
.contact-mini .row{display:flex;gap:14px;align-items:center}
.contact-mini .dot{display:inline-block;width:12px;height:12px;border-radius:50%;background:var(--green);vertical-align:middle;margin-right:5px}
.contact-mini .dot.b{background:var(--navy)}
.brand{position:absolute;left:50%;transform:translateX(-50%);text-align:center;font-weight:800;color:var(--navy);letter-spacing:2px}
.brand .mark{display:inline-block;width:14px;height:14px;border-radius:50%;background:var(--pink);margin-right:8px;vertical-align:middle}
.site-header .brand{top:30px;font-size:26px}
.notch{position:absolute;left:520px;top:70px;width:160px;height:70px;background:#fff;border-radius:0 0 80px 80px;z-index:2}
.cta-mini{position:absolute;top:40px;display:flex;align-items:center;gap:8px;font-size:10px;font-weight:700;color:var(--navy);line-height:1.2}
.cta-mini .ic{width:30px;height:30px;border-radius:50%;display:flex;align-items:center;justify-content:center}

/* hero */
.hero{position:absolute;top:106px;left:0;width:1200px;height:512px;background:linear-gradient(180deg,#6e4a3a 0%,#b06b43 22%,#3d3340 55%,#1d2024 100%)}
.hero-shade{position:absolute;inset:0;background:linear-gradient(90deg,rgba(0,0,0,.35),rgba(0,0,0,.1))}
.hero h1{position:absolute;left:144px;top:322px;color:#fff;font-size:31px;font-weight:800;line-height:1.25;letter-spacing:.5px}
.hero p{position:absolute;left:144px;top:408px;color:#cfe8f2;font-size:15px;font-weight:700;line-height:1.35;letter-spacing:.5px}
.contact-box{position:absolute;left:738px;top:53px;width:318px;height:406px;background:rgba(25,25,25,.88);padding:20px 26px}
.contact-box h2{color:#fff;font-size:22px;font-weight:700;letter-spacing:1px;margin-bottom:16px}
.field{height:38px;border:1px solid #bbb;background:rgba(255,255,255,.04);margin-bottom:12px;display:flex;align-items:center;padding:0 12px;gap:10px;color:#ddd;font-size:10px;font-weight:600}
.field .gd{width:12px;height:12px;border-radius:50%;background:var(--green)}
.field.msg{height:100px;align-items:flex-start;padding-top:12px}
.contact-box .btn{width:266px;height:46px;background:var(--orange);font-size:18px;margin-top:8px}

/* intro */
.intro{position:absolute;top:618px;left:0;width:1200px;height:600px}
.ph{display:block}
.intro .ph{position:absolute;left:143px;top:60px;width:457px;height:459px;background:linear-gradient(135deg,#d9dde0,#8d9aa3 60%,#5b666d)}
.intro .text{position:absolute;left:660px;top:122px;width:400px}
.intro h2{font-size:22px;font-weight:800;line-height:1.3;margin:16px 0 26px;color:var(--ink)}
.intro p{font-size:13.5px;line-height:1.6;color:var(--muted);margin-bottom:18px}

/* vision */
.vision{position:absolute;top:1218px;left:0;width:1200px;height:910px;background:var(--teal)}
.vision .rule{background:#fff;position:absolute;left:144px;top:100px}
.vision h2{position:absolute;left:144px;top:112px;color:#fff;font-size:24px;font-weight:800}
.vision .lead{position:absolute;left:144px;top:160px;width:340px;color:#fff;font-size:13px;font-weight:700;line-height:1.45}
.vision .body{position:absolute;left:144px;top:222px;width:340px;color:#e3f4fa;font-size:13px;line-height:1.5}
.vision .btn{position:absolute;left:150px;top:378px;width:340px;height:56px;background:var(--green);font-size:14px;box-shadow:0 0 0 4px rgba(255,255,255,.35)}
.vision .ph{position:absolute;left:577px;top:68px;width:482px;height:396px;background:linear-gradient(160deg,#8fb9d4,#6f8f7a 45%,#4f6f55);box-shadow:0 10px 30px rgba(0,0,0,.3)}
.services{position:absolute;left:142px;top:524px;display:grid;grid-template-columns:repeat(4,222px);grid-auto-rows:156px;gap:12px 10px}
.tile{background:var(--teal-tile);display:flex;flex-direction:column;align-items:center;justify-content:center;gap:22px;color:#fff;font-size:13px;font-weight:700;text-transform:uppercase}

/* specialist + gallery */
.specialist{position:absolute;top:2128px;left:0;width:1200px;height:1179px;background:var(--light)}
.specialist .rule{position:absolute;left:565px;top:82px}
.specialist h2{position:absolute;left:0;width:1200px;top:100px;text-align:center;font-size:24px;font-weight:800}
.specialist .book{position:absolute;left:468px;top:162px;width:280px;height:54px;background:var(--orange);font-size:15px}
.gallery{position:absolute;left:142px;top:280px;display:grid;grid-template-columns:repeat(3,302px);grid-auto-rows:246px;gap:6px}
.gallery .ph{width:100%;height:100%}
.specialist .more{position:absolute;left:520px;top:1080px;width:178px;height:48px;background:var(--pink);font-size:15px}

/* buildings */
.buildings{position:absolute;top:3307px;left:0;width:1200px;height:463px;text-align:center}
.buildings svg{position:absolute;left:564px;top:82px}
.buildings h2{position:absolute;top:185px;width:1200px;font-size:25px;font-weight:800;line-height:1.2}
.buildings p{position:absolute;top:276px;width:1200px;font-size:15px;line-height:1.75;color:var(--muted)}
.buildings .btn{position:absolute;left:508px;top:346px;width:184px;height:56px;background:var(--orange);font-size:15px}

/* builder */
.builder{position:absolute;top:3770px;left:0;width:1200px;height:565px;background:linear-gradient(180deg,#2c3138,#1c2025)}
.builder .rule{position:absolute;left:565px;top:72px}
.builder h2{position:absolute;top:88px;width:1200px;text-align:center;color:#fff;font-size:25px;font-weight:700}
.builder p{position:absolute;left:380px;top:142px;width:440px;text-align:center;color:#d6d6d6;font-size:14px;line-height:1.5}
.stats{position:absolute;left:162px;top:265px;display:grid;grid-template-columns:repeat(4,207px);gap:22px}
.stat{height:228px;border:2px solid #d8d8d8;display:flex;flex-direction:column;align-items:center;justify-content:flex-end;padding-bottom:28px;color:#fff;text-align:center}
.stat svg{margin-bottom:24px}
.stat strong{font-size:26px;font-weight:800;line-height:1.05}
.stat span{font-size:12px;font-weight:700;margin-top:8px;text-transform:uppercase;line-height:1.3}

/* form */
.help{position:absolute;top:4335px;left:0;width:1200px;height:680px;text-align:center}
.help h3{position:absolute;top:99px;width:1200px;font-size:17px;font-weight:800}
.help h2{position:absolute;top:122px;width:1200px;font-size:25px;font-weight:800}
.help p{position:absolute;top:168px;width:1200px;font-size:14px;color:var(--muted)}
.help .in{position:absolute;left:367px;width:466px;height:48px;border:1px solid #aaa;text-align:left;padding:14px 14px;font-size:12px;color:#555}
.help .btn{position:absolute;left:539px;top:500px;width:122px;height:54px;background:var(--orange);font-size:15px}

/* footer */
.skyline{position:absolute;top:4920px;left:0;width:1200px;height:110px}
.site-footer{position:absolute;top:5015px;left:0;width:1200px;height:237px;background:#fff}
.addr{position:absolute;left:142px;font-size:11px;line-height:1.45;color:var(--muted)}
.addr b{color:var(--navy);font-size:13px;display:block}
.site-footer .brand{top:80px;font-size:30px}
.site-footer .green{position:absolute;left:820px;top:38px;width:150px;height:30px;background:var(--green);font-size:14px}
.foot-phones{position:absolute;left:820px;top:84px;font-size:11px;color:var(--muted);display:flex;gap:14px}
.bottom-bar{position:absolute;top:5252px;left:0;width:1200px;height:42px;background:var(--dark);color:#ddd;font-size:10px;display:flex;align-items:center;justify-content:space-between;padding:0 32px 0 28px}
.bottom-bar nav{display:flex;gap:34px;font-weight:700}
.bottom-bar em{font-style:normal;color:var(--pink)}
</style>
</head>
<body>

<header class="site-header">
  <div class="contact-mini">
    <span class="pill">BEM ATENDIMENTO</span>
    <div class="row"><span><i class="dot"></i>+55 21 4000-2718</span><span><i class="dot b"></i>+1 (305) 555-0147</span></div>
  </div>
  <div class="brand"><span class="mark"></span>CORAL PARLOR</div>
  <div class="cta-mini" style="left:772px"><span class="ic" style="background:var(--pink)"><svg width="14" height="14" viewBox="0 0 24 24"><path fill="#fff" d="M6.6 10.8a15 15 0 0 0 6.6 6.6l2.2-2.2a1 1 0 0 1 1-.25 11.4 11.4 0 0 0 3.6.6 1 1 0 0 1 1 1V20a1 1 0 0 1-1 1A17 17 0 0 1 3 4a1 1 0 0 1 1-1h3.5a1 1 0 0 1 1 1c0 1.25.2 2.45.6 3.6a1 1 0 0 1-.25 1z"/></svg></span>FALE COM UM<br>AGENTE</div>
  <div class="cta-mini" style="left:910px"><span class="ic" style="background:var(--teal)"><svg width="14" height="14" viewBox="0 0 24 24"><rect x="3" y="5" width="18" height="16" rx="2" fill="#fff"/><rect x="3" y="5" width="18" height="4" fill="#cfe"/></svg></span>AGENDE UMA<br>CONVERSA</div>
</header>

<section class="hero">
  <div class="ph" role="img" aria-label="Casa de luxo com piscina ao entardecer na Flórida" style="position:absolute;inset:0"></div>
  <div class="hero-shade"></div>
  <div class="notch" style="top:-36px"></div>
  <h1>INVISTA NA FLORIDA<br>E RENTABILIZE TRANQUILIDADE</h1>
  <p>CONHEÇA AS MELHORES OPORTUNIDADES DE<br>INVESTIMENTOS NA FLÓRIDA</p>
  <form class="contact-box">
    <h2>CONTACT US</h2>
    <div class="field"><i class="gd"></i>NAME</div>
    <div class="field"><i class="gd"></i>E-MAIL</div>
    <div class="field"><i class="gd"></i>PHONE</div>
    <div class="field msg"><i class="gd"></i>MESSAGE</div>
    <button class="btn" type="button">SUBMIT</button>
  </form>
</section>

<section class="intro">
  <div class="ph" role="img" aria-label="Lounge moderno com poltronas e painéis de imóveis"></div>
  <div class="text">
    <div class="rule"></div>
    <h2>PRESENTES NO BRASIL E<br>ESTADOS UNIDOS</h2>
    <p>O The Coral Parlor possui um Lounge permanente no Rio de Janeiro, Brasil e em Orlando, na Flórida. Com um conceito inovador de atendimento 360º, assessorando os clientes que desejam comprar um imóvel nos Estados Unidos, seja para investir ou Morar.</p>
    <p>Com a parceria exclusiva da Stonegate Homes, a maior construtora dos Estados Unidos, garantimos as melhores escolhas para você e sua família! Nossos especialistas possuem visão 360º para apoiá-lo em todo o processo e viver a melhor experiência na compra de um imóvel na América.</p>
  </div>
</section>

<section class="vision">
  <div class="rule"></div>
  <h2>VISÃO 360º</h2>
  <p class="lead">Cuidamos de absolutamente tudo para você se sentir em casa na Florida!</p>
  <p class="body">Atendimento 360º de brasileiro para brasileiro. Nossos especialistas irão lhe auxiliar em tudo o que você precisar para concretizar seu sonho de investir ou viver na América, com todo conforto e principalmente segurança. Desde a escolha do melhor imóvel até abertura de empresas e remessas financeiras.</p>
  <a class="btn"><svg width="26" height="26" viewBox="0 0 24 24"><circle cx="12" cy="12" r="11" fill="#fff"/><path fill="var(--green)" d="M8.5 7.5c.6-.4 1.2 0 1.4.6l.5 1.3c.1.4 0 .7-.3 1l-.5.5a7 7 0 0 0 3.5 3.5l.5-.5c.3-.3.6-.4 1-.3l1.3.5c.6.2 1 .8.6 1.4-.6 1-1.7 1.5-2.8 1.1A10 10 0 0 1 7.4 10.3c-.4-1.1.1-2.2 1.1-2.8z"/></svg>DESEJA FALAR VIA ZAPLINE?</a>
  <div class="ph" role="img" aria-label="Vista aérea de condomínio residencial na Flórida"></div>
  <div class="services">
    <div class="tile"><svg width="40" height="40" viewBox="0 0 40 40" fill="none" stroke="#fff" stroke-width="2"><rect x="6" y="14" width="28" height="20"/><path d="M20 4v10M14 24h12"/></svg>Financiamento</div>
    <div class="tile"><svg width="40" height="40" viewBox="0 0 40 40" fill="none" stroke="#fff" stroke-width="2"><rect x="10" y="4" width="20" height="32" rx="2"/><circle cx="20" cy="16" r="4"/><path d="M14 28h12"/></svg>Vistos</div>
    <div class="tile"><svg width="40" height="40" viewBox="0 0 40 40" fill="none" stroke="#fff" stroke-width="2"><rect x="8" y="4" width="24" height="32" rx="2"/><rect x="12" y="8" width="16" height="6"/><path d="M13 20h2M19 20h2M25 20h2M13 26h2M19 26h2M25 26h2"/></svg>Contabilidade</div>
    <div class="tile"><svg width="40" height="40" viewBox="0 0 40 40" fill="none" stroke="#fff" stroke-width="2"><path d="M6 20h28v10H6zM10 20v-8h20v8M8 30v4M32 30v4"/></svg>Mobília</div>
    <div class="tile"><svg width="40" height="40" viewBox="0 0 40 40" fill="none" stroke="#fff" stroke-width="2"><path d="M10 4h16l6 6v26H10z"/><path d="M15 16h12M15 22h12M15 28h8"/></svg>Remessas Financeiras</div>
    <div class="tile"><svg width="40" height="40" viewBox="0 0 40 40" fill="none" stroke="#fff" stroke-width="2"><rect x="4" y="8" width="32" height="24" rx="2"/><circle cx="14" cy="18" r="4"/><path d="M22 16h10M22 22h10M9 27h10"/></svg>EB-5 (Green Card)</div>
    <div class="tile"><svg width="40" height="40" viewBox="0 0 40 40" fill="none" stroke="#fff" stroke-width="2"><path d="M4 14h32v20H4zM8 14V8h24v6M16 22h8"/></svg>Documentações</div>
    <div class="tile"><svg width="40" height="40" viewBox="0 0 40 40"><path fill="#fff" d="M20 4 3 19h5v16h9V25h6v10h9V19h5z"/></svg>Administração de Casas</div>
  </div>
</section>

<section class="specialist">
  <div class="rule"></div>
  <h2>DESEJA FALAR COM UM ESPECIALISTA?</h2>
  <a class="btn book"><svg width="18" height="18" viewBox="0 0 24 24" fill="none" stroke="#fff" stroke-width="2"><rect x="3" y="5" width="18" height="16"/><path d="M3 10h18M8 3v4M16 3v4"/></svg>AGENDAR ATENDIMENTO</a>
  <div class="gallery">
    <div class="ph" role="img" aria-label="Área de lazer coberta com bar" style="background:linear-gradient(160deg,#5a4636,#a27a52)"></div>
    <div class="ph" role="img" aria-label="Casa com piscina ao anoitecer" style="background:linear-gradient(180deg,#c07a55,#463a45)"></div>
    <div class="ph" role="img" aria-label="Portal de entrada de condomínio" style="background:linear-gradient(180deg,#4f8fd0,#7d8a6a)"></div>
    <div class="ph" role="img" aria-label="Casa iluminada ao entardecer" style="background:linear-gradient(180deg,#3b4a6e,#8a6a52)"></div>
    <div class="ph" role="img" aria-label="Clubhouse noturno" style="background:linear-gradient(180deg,#2a3658,#9a6b46)"></div>
    <div class="ph" role="img" aria-label="Piscina com palmeiras" style="background:linear-gradient(180deg,#7fb3d8,#3aa2b8)"></div>
    <div class="ph" role="img" aria-label="Cozinha moderna" style="background:linear-gradient(160deg,#9a9a98,#4e4c48)"></div>
    <div class="ph" role="img" aria-label="Fachada de casa de dois andares" style="background:linear-gradient(180deg,#a9c4dc,#9aa199)"></div>
    <div class="ph" role="img" aria-label="Sala de estar com sofás" style="background:linear-gradient(160deg,#e2ddd6,#9c8f82)"></div>
  </div>
  <a class="btn more">SHOW MORE <svg width="12" height="12" viewBox="0 0 12 12"><path d="M2 4l4 4 4-4" stroke="#fff" stroke-width="2" fill="none"/></svg></a>
</section>

<section class="buildings">
  <svg width="72" height="80" viewBox="0 0 72 80" fill="none" stroke="var(--teal)" stroke-width="3"><rect x="6" y="34" width="22" height="44"/><rect x="28" y="6" width="26" height="72"/><rect x="54" y="26" width="14" height="52"/><path d="M34 16h4M44 16h4M34 28h4M44 28h4M34 40h4M44 40h4M34 52h4M44 52h4M12 44h4M20 44h4M12 56h4M20 56h4"/></svg>
  <h2>RECEIVES PRICES AND<br>PLANTS OF BUILDINGS</h2>
  <p>Have at your disposal information about our properties.<br>You will have an always up-to-date list of our available launches and homes.</p>
  <a class="btn">REQUEST HERE</a>
</section>

<section class="builder">
  <div class="ph" role="img" aria-label="Condomínio residencial ao entardecer ao fundo" style="position:absolute;inset:0;opacity:.35;background:linear-gradient(180deg,#404a58,#202428)"></div>
  <div class="rule"></div>
  <h2>STONEGATE</h2>
  <p>STONEGATE é mais do que uma simples construtora imobiliária. É uma das maiores construtoras dos ESTADOS UNIDOS. O compromisso com a qualidade, valor e integridade é a base fundamental. Os condomínios construídos pela STONEGATE atendem a todos os estilos de vida.</p>
  <div class="stats">
    <div class="stat"><svg width="40" height="44" viewBox="0 0 40 44"><rect x="6" y="2" width="28" height="42" fill="#fff"/><g fill="#2c3138"><rect x="11" y="8" width="5" height="5"/><rect x="24" y="8" width="5" height="5"/><rect x="11" y="18" width="5" height="5"/><rect x="24" y="18" width="5" height="5"/><rect x="17" y="32" width="6" height="12"/></g></svg><strong>40+</strong><span>Cidades</span></div>
    <div class="stat"><svg width="44" height="44" viewBox="0 0 44 44"><circle cx="22" cy="22" r="20" fill="#fff"/><path d="M10 14l10 4 4 10-8 6zM28 8l6 10-6 4z" fill="#2c3138"/></svg><strong>18</strong><span>Estados</span></div>
    <div class="stat"><svg width="44" height="40" viewBox="0 0 44 40"><rect x="2" y="10" width="40" height="28" rx="3" fill="#fff"/><path d="M15 10V4h14v6" stroke="#fff" stroke-width="3" fill="none"/><rect x="18" y="20" width="8" height="6" fill="#2c3138"/></svg><strong>EM 1954</strong><span>Fundada</span></div>
    <div class="stat"><svg width="44" height="44" viewBox="0 0 44 44" fill="#fff"><rect x="4" y="8" width="36" height="12"/><rect x="8" y="20" width="4" height="22"/><rect x="32" y="20" width="4" height="22"/><rect x="6" y="4" width="4" height="6"/><rect x="34" y="4" width="4" height="6"/></svg><strong>MAIS<br>DE 600</strong><span>Condomínios em<br>construção</span></div>
  </div>
</section>

<section class="help">
  <h3>ESTAMOS AQUI PARA AJUDAR VOCÊ</h3>
  <h2>NO QUE VOCÊ PRECISAR</h2>
  <p>Não hesite em falar com um de nossos especialistas.</p>
  <div class="in" style="top:224px">Nome Completo</div>
  <div class="in" style="top:284px">eMail</div>
  <div class="in" style="top:344px;height:138px">Mensagem</div>
  <a class="btn">ENVIAR</a>
</section>

<div class="skyline" role="img" aria-label="Silhueta suave de cidade e roda-gigante" style="background:linear-gradient(180deg,rgba(255,255,255,0),#e9e9ea)"></div>

<footer class="site-footer">
  <div class="addr" style="top:38px"><b><svg width="10" height="13" viewBox="0 0 10 13"><path d="M5 0a5 5 0 0 0-5 5c0 4 5 8 5 8s5-4 5-8a5 5 0 0 0-5-5z" fill="var(--pink)"/></svg> Atlântica Center</b>Av. das Palmeiras 1200, Loja 210<br>Barra da Tijuca – RJ – Brasil</div>
  <div class="addr" style="top:112px"><b><svg width="10" height="13" viewBox="0 0 10 13"><path d="M5 0a5 5 0 0 0-5 5c0 4 5 8 5 8s5-4 5-8a5 5 0 0 0-5-5z" fill="var(--pink)"/></svg> Orlando</b>4820 Lakeview Parkway, Suite 300, Orlando, FL</div>
  <div class="addr" style="top:166px">✉ contato@coralparlor-mail.com</div>
  <div class="brand"><span class="mark"></span>CORAL PARLOR</div>
  <a class="btn green">BEM +1 (305) 555-0147</a>
  <div class="foot-phones"><span>+55 21 4000-2718</span><span>+1 (305) 555-0147</span></div>
  <div class="cta-mini" style="left:820px;top:118px"><span class="ic" style="background:var(--pink)"></span>FALE COM UM<br>AGENTE</div>
  <div class="cta-mini" style="left:950px;top:118px"><span class="ic" style="background:var(--teal)"></span>AGENDE UMA<br>CONVERSA</div>
</footer>

<div class="bottom-bar">
  <span>© 2017 · THE CORAL PARLOR BY <em>NORTEVIA</em></span>
  <nav><span>HOME</span><span>IMÓVEIS</span><span>PARCEIROS</span><span>CONTATO</span><span>TERMOS DE USO</span></nav>
  <em>◆</em>
</div>

</body>
</html>
```